VORLAND COMPOSITES INC website in USA

VORLAND COMPOSITES INC incorporated and operated in USA needs a completely new design of website. This Wyoming based company is a importer and distributor of composites material to supply mainly to American and Canadian/Mexican customers. Our main products includes Carbon Fiber, Aramid Fiber, Glass Fiber, Basalt Fiber, High Silica Glass, Quartz Fiber, S-Glass, Alumina Fiber, Vacuum Auxiliary.

We are one stop composites solution provider for Automotive, Aerospace, Construction, Electrical and Machinery industries.

We are exclusive sales company in North America for BLORAN composites produced from China and their other Asia facilities.

Target Market(s)

USA and Canada

Industry/Entity Type

Composites materials

Coding

Coded - Design and coding required

Number of Pages Required

5+ page

Requirements
Nice to have
• Color theme to match our corporate logo VORLAND. VORLAND stands for Northgate Provisioning Trade Holdings

```html
<!DOCTYPE html>
<html lang="en">
<head>
<meta charset="utf-8">
<title>VORLAND COMPOSITES INC — Website Pages</title>
<link href="https://fonts.googleapis.com/css2?family=Inter:wght@400;500;600;700&display=swap" rel="stylesheet">
<style>
:root{
  --board:#8b8b8b;
  --bg:#0a1019;
  --bg-deep:#080d15;
  --card:#0e1722;
  --line:#1a2532;
  --accent:#22d3f2;
  --accent-ink:#04202a;
  --text:#eef3f8;
  --muted:#a9b6c3;
}
*{box-sizing:border-box;margin:0;padding:0}
html,body{width:1200px;height:538px;overflow:hidden}
body{background:var(--board);font-family:"Inter",sans-serif;color:var(--text);position:relative}
.page{position:absolute;width:790px;background:var(--bg);transform:scale(.4658);transform-origin:0 0;box-shadow:0 8px 24px rgba(0,0,0,.35);overflow:hidden}
.page--home{left:29px;top:29px;height:1031px}
.page--products{left:416px;top:29px;height:523px}
.page--about{left:803px;top:29px;height:523px}
.page--industries{left:416px;top:292px;height:466px}
.page--contact{left:803px;top:292px;height:466px}
.wrap{width:558px;margin-left:116px}

/* header */
.site-header{height:31px;border-bottom:1px solid var(--line);display:flex;align-items:center;justify-content:space-between;padding:0 106px 0 116px}
.brand{display:flex;align-items:center;gap:6px}
.brand-dot{width:23px;height:23px;border-radius:50%;border:1.5px solid var(--text)}
.brand-name{font-size:7.5px;font-weight:700;color:var(--accent);line-height:1.1}
.brand-sub{font-size:4px;color:var(--muted)}
.nav{display:flex;align-items:center;gap:4px}
.nav a{font-size:6px;color:var(--accent);text-decoration:none;padding:4px 6px;border-radius:3px}
.nav a.is-active{background:#1a2634;color:var(--muted);font-size:4.5px}
.nav a.quote{background:var(--accent);color:var(--accent-ink);font-weight:500}

/* shared */
.btn{display:inline-block;background:var(--accent);color:var(--accent-ink);font-size:6px;font-weight:500;padding:5px 8px;border-radius:9px;white-space:nowrap}
.btn-ghost{display:inline-block;color:var(--text);font-size:6px;padding:5px 8px;border-radius:9px;background:#0f1a26;white-space:nowrap}
.chip{display:inline-block;font-size:5.5px;padding:5px 6px;border:1px solid var(--line);border-radius:4px;background:var(--card);margin-right:5px}
.tag{display:inline-block;font-size:4px;color:var(--muted);padding:3px 5px;border:1px solid var(--line);border-radius:6px;background:var(--card)}
.card{background:var(--card);border:1px solid var(--line);border-radius:4px;padding:8px 8px;height:59px;overflow:hidden}
.card--tall{height:69px}
.card--short{height:48px}
.card h3{font-size:9px;font-weight:600;margin-bottom:5px;line-height:1.2}
.card p{font-size:5.5px;line-height:1.85;color:#dfe6ee}
.grid3{display:grid;grid-template-columns:repeat(3,1fr);gap:10px}
.section{border-top:1px solid var(--line);overflow:hidden}
.section-title{font-size:13.5px;font-weight:600}
.band{display:flex;justify-content:space-between;align-items:center;background:linear-gradient(90deg,#0f1a26,#0c1520);border-radius:6px;padding:7px 9px}
.band p{font-size:5.5px}
.band b{font-weight:600}
.page-title{font-size:19.5px;font-weight:600;margin-top:24px}
.page-sub{font-size:5.5px;color:#dfe6ee;margin-top:8px;line-height:1.6}

/* footer */
.site-footer{position:absolute;left:0;right:0;bottom:0;height:123px;border-top:1px solid var(--line);padding:13px 0 0 116px;display:grid;grid-template-columns:278px 144px 140px;background:var(--bg-deep)}
.site-footer .brand{margin-top:8px}
.foot-note{font-size:5.5px;margin-top:10px;color:#dfe6ee}
.foot-head{font-size:9px;font-weight:600;margin-bottom:13px}
.foot-links a{display:block;font-size:5.5px;color:var(--accent);text-decoration:none;margin-bottom:9px}
.foot-office p{font-size:5.5px;margin-bottom:9px}
.foot-office .mail,.foot-office .tel{color:var(--accent)}
.foot-office small{font-size:3.8px;color:var(--muted)}

/* home */
.hero{display:flex;justify-content:space-between;padding-top:29px;height:247px}
.hero-copy{width:330px;padding-top:6px}
.hero h1{font-size:19.5px;font-weight:700;line-height:1.12;margin:5px 0 6px;letter-spacing:-.2px}
.hero h1 span{color:var(--accent)}
.hero-lead{font-size:5.6px;line-height:1.7;margin-bottom:7px}
.hero-actions{margin-bottom:7px}
.hero-chips .chip{margin-bottom:5px}
.hero-visual{width:219px;height:188px;border-radius:6px;background:linear-gradient(180deg,#5b6f8d 0%,#b48a86 35%,#7a7d88 55%,#3e4550 100%)}
.block{padding-top:22px}
.block-head{display:flex;justify-content:space-between;align-items:center;height:20px;margin-bottom:10px}
.tags{display:flex;gap:4px}
.rows{display:grid;gap:10px}
.section--why{height:145px}
.section--core{height:205px}
.section--cta{height:85px}
.section--served{height:195px}
.section--served .block{padding-top:21px}
.section--served .block-head{margin-bottom:12px}
.home-cta{padding-top:32px}
.home-cta .band{margin-left:-8px}
.products-grid .card{height:auto;min-height:60px}
.products-grid .card--tall{min-height:68px}

/* industries table */
.ind-table{width:100%;border-collapse:separate;border-spacing:0 3px;margin-top:22px;font-size:5.3px}
.ind-table th{text-align:left;font-weight:500;padding:0 5px 4px}
.ind-table td{background:var(--card);border-top:1px solid var(--line);border-bottom:1px solid var(--line);padding:7px 5px;border-left:1px solid var(--line)}

/* form */
.rfq{display:grid;grid-template-columns:1fr 1fr;gap:7px 7px;margin-top:20px}
.field label{display:block;font-size:5.5px;margin-bottom:4px}
.field .input{height:15px;border:1px solid var(--line);background:var(--card);border-radius:3px;font-size:4px;color:var(--muted);padding:5px 6px;display:flex;justify-content:space-between}
.field--wide{grid-column:1/3}
.field .textarea{height:48px;font-family:monospace}
.submit{font-size:4px;padding:4px 8px;margin-top:6px}
</style>
</head>
<body>

<!-- Home -->
<section class="page page--home">
  <header class="site-header">
    <div class="brand"><span class="brand-dot"></span><div><div class="brand-name">VORLAND COMPOSITES INC</div><div class="brand-sub">Wyoming · North America Distributor</div></div></div>
    <nav class="nav"><a class="is-active">Home</a><a>Products</a><a>Industries</a><a>About</a><a>Contact</a><a class="quote">Request a Quote</a></nav>
  </header>
  <div class="wrap">
    <div class="hero">
      <div class="hero-copy">
        <span class="tag">Exclusive BLORAN Partner · USA · Canada · Mexico</span>
        <h1>One-stop composites supply for <span>Aerospace, Automotive, Construction &amp; Energy</span></h1>
        <p class="hero-lead">Stock + custom weaves, unidirectional, multiaxials, and high-temp fibers with technical documentation, QA traceability, and North American logistics.</p>
        <div class="hero-actions"><span class="btn">Browse Products</span> <span class="btn-ghost">Request a Quote</span></div>
        <div class="hero-chips"><span class="chip">Carbon • Aramid • Glass • Basalt</span><span class="chip">High Silica • Quartz • S-Glass</span><br><span class="chip">Alumina • Vacuum Auxiliary</span></div>
      </div>
      <div class="hero-visual" role="img" aria-label="Photo of a city skyline at dusk above rows of composite fabric rolls"></div>
    </div>
  </div>
  <div class="section section--why"><div class="wrap block">
    <div class="block-head"><h2 class="section-title">Why VORLAND</h2><div class="tags"><span class="tag">Certs &amp; COAs</span><span class="tag">Rapid Lead Times</span><span class="tag">Multi-industry Expertise</span></div></div>
    <div class="grid3">
      <div class="card card--tall"><h3>Exclusive BLORAN Access</h3><p>Priority access to BLORAN composite lines manufactured in Asia with QA traceability and export documentation tuned for North America.</p></div>
      <div class="card card--tall"><h3>Engineering-grade Catalog</h3><p>From PAN-based carbon to high-temperature silica and alumina fibers, our breadth covers performance, process, and budget envelopes.</p></div>
      <div class="card card--tall"><h3>Vacuum &amp; Processing</h3><p>Vacuum bagging films, peel plies, release media, and ancillary supplies for prepreg, infusion, and OOA processes—bundled to your BOM.</p></div>
    </div>
  </div></div>
  <div class="section section--core"><div class="wrap block">
    <div class="block-head"><h2 class="section-title">Core Product Families</h2><span class="btn-ghost">Full catalog</span></div>
    <div class="rows">
      <div class="grid3">
        <div class="card"><h3>Carbon Fiber</h3><p>Woven, UD, multiaxial, and prepreg-ready reinforcements for structural applications.</p></div>
        <div class="card"><h3>Aramid Fiber</h3><p>Impact-resistant fabrics for ballistic and abrasion environments.</p></div>
        <div class="card"><h3>Glass &amp; S-Glass</h3><p>E-glass and S-glass options balancing cost and performance.</p></div>
      </div>
      <div class="grid3">
        <div class="card"><h3>Basalt Fiber</h3><p>Naturally derived high-strength fibers with thermal stability.</p></div>
        <div class="card"><h3>High Silica &amp; Quartz</h3><p>High-temperature and dielectric-stable reinforcements.</p></div>
        <div class="card"><h3>Alumina Fiber</h3><p>Ceramic fibers for extreme heat and wear environments.</p></div>
      </div>
    </div>
  </div></div>
  <div class="section section--cta"><div class="wrap home-cta">
    <div class="band"><p><b>Need specification support?</b> Our team can map your mechanical targets to the right fiber/weave and process route.</p><span class="btn">Talk to Engineering</span></div>
  </div></div>
  <div class="section section--served"><div class="wrap block">
    <div class="block-head"><h2 class="section-title">Industries Served</h2></div>
    <div class="rows">
      <div class="grid3">
        <div class="card"><h3>Aerospace</h3><p>Prepreg, OOA, autoclave, and interior panels.</p></div>
        <div class="card"><h3>Automotive</h3><p>Body panels, monocoques, interior trims, and tooling.</p></div>
        <div class="card"><h3>Construction</h3><p>Rebar wraps, FRP plates, strengthening systems.</p></div>
      </div>
      <div class="grid3">
        <div class="card card--short"><h3>Electrical</h3><p>Dielectric laminates and thermal insulation stacks.</p></div>
        <div class="card card--short"><h3>Machinery</h3><p>Lightweight arms, guards, and high-temp housings.</p></div>
        <div class="card card--short"><h3>Energy</h3><p>Wind blades, tanks, and insulation jackets.</p></div>
      </div>
    </div>
  </div></div>
  <footer class="site-footer">
    <div><div class="brand"><span class="brand-dot"></span><div><div class="brand-name">VORLAND COMPOSITES INC</div><div class="brand-sub">Wyoming · North America Distributor</div></div></div><p class="foot-note">Exclusive North America sales partner for BLORAN Composites.</p></div>
    <div><h4 class="foot-head">Explore</h4><div class="foot-links"><a>Product Catalog</a><a>Industries</a><a>About</a><a>Contact</a></div></div>
    <div class="foot-office"><h4 class="foot-head">Head Office</h4><p>Redmesa City, USA</p><p class="mail">sales@vorlandcomposites.com</p><p class="tel">+1 (555) 014-0188</p><small>© 2025 VORLAND COMPOSITES INC. All rights reserved.</small></div>
  </footer>
</section>

<!-- Products -->
<section class="page page--products">
  <header class="site-header">
    <div class="brand"><span class="brand-dot"></span><div><div class="brand-name">VORLAND COMPOSITES INC</div><div class="brand-sub">Wyoming · North America Distributor</div></div></div>
    <nav class="nav"><a>Home</a><a class="is-active">Products</a><a>Industries</a><a>About</a><a>Contact</a><a class="quote">Request a Quote</a></nav>
  </header>
  <div class="wrap">
    <h1 class="page-title">Product Catalog</h1>
    <p class="page-sub">Below is a quick overview. Specification sheets are available on request.</p>
    <div class="rows products-grid" style="margin-top:14px">
      <div class="grid3">
        <div class="card card--tall"><h3>Carbon Fiber</h3><p>Plain/Twill weaves, UD tapes, multiaxials; surface treatments for epoxy, vinyl ester, and thermoplastic matrices.</p></div>
        <div class="card card--tall"><h3>Aramid Fiber</h3><p>Para-aramid fabrics for ballistic/impact; hybrid with carbon or glass for tuned stiffness and toughness.</p></div>
        <div class="card card--tall"><h3>Glass Fiber</h3><p>E-glass woven/stitched fabrics; surfacing veils; electrical grade options.</p></div>
      </div>
      <div class="grid3">
        <div class="card"><h3>Basalt Fiber</h3><p>Continuous basalt fabrics for chemical and thermal resistance.</p></div>
        <div class="card"><h3>High Silica Glass</h3><p>90–96% silica content for high-temperature insulation and fire barriers.</p></div>
        <div class="card"><h3>Quartz Fiber</h3><p>Ultrapure silica fibers with excellent dielectric properties.</p></div>
      </div>
      <div class="grid3">
        <div class="card"><h3>S-Glass</h3><p>High-strength glass reinforcement for aerospace and defense.</p></div>
        <div class="card"><h3>Alumina Fiber</h3><p>Ceramic fibers for extreme thermal stability and wear.</p></div>
        <div class="card"><h3>Vacuum Auxiliary</h3><p>Bagging films, release fabrics, peel plies, breather, sealant tapes, infusion media, connectors.</p></div>
      </div>
    </div>
    <div class="band" style="margin-top:12px"><p><b>Don't see a weave listed?</b> We can source equivalent or custom fabrics to your spec.</p><span class="btn">Request Data Sheet</span></div>
  </div>
  <footer class="site-footer">
    <div><div class="brand"><span class="brand-dot"></span><div><div class="brand-name">VORLAND COMPOSITES INC</div><div class="brand-sub">Wyoming · North America Distributor</div></div></div><p class="foot-note">Exclusive North America sales partner for BLORAN Composites.</p></div>
    <div><h4 class="foot-head">Explore</h4><div class="foot-links"><a>Product Catalog</a><a>Industries</a><a>About</a><a>Contact</a></div></div>
    <div class="foot-office"><h4 class="foot-head">Head Office</h4><p>Redmesa City, USA</p><p class="mail">sales@vorlandcomposites.com</p><p class="tel">+1 (555) 014-0188</p><small>© 2025 VORLAND COMPOSITES INC. All rights reserved.</small></div>
  </footer>
</section>

<!-- About -->
<section class="page page--about">
  <header class="site-header">
    <div class="brand"><span class="brand-dot"></span><div><div class="brand-name">VORLAND COMPOSITES INC</div><div class="brand-sub">Wyoming · North America Distributor</div></div></div>
    <nav class="nav"><a>Home</a><a>Products</a><a>Industries</a><a class="is-active">About</a><a>Contact</a><a class="quote">Request a Quote</a></nav>
  </header>
  <div class="wrap">
    <h1 class="page-title">About VORLAND</h1>
    <p class="page-sub">VORLAND COMPOSITES INC is incorporated in Wyoming, USA and serves customers across the United States, Canada, and Mexico. We import and distribute a full spectrum of composite reinforcements and process consumables with technical support and documentation tailored to North American requirements.</p>
    <div class="grid3" style="margin-top:14px">
      <div class="card card--tall"><h3>Exclusive BLORAN Sales</h3><p>We are the exclusive sales company in North America for BLORAN composites manufactured in China and other Asia facilities.</p></div>
      <div class="card card--tall"><h3>Quality &amp; Traceability</h3><p>COAs, batch traceability, and export paperwork aligned with customer QA systems.</p></div>
      <div class="card card--tall"><h3>Logistics Optimized</h3><p>Consolidation, bonded warehousing, and expedited routes for critical programs.</p></div>
    </div>
  </div>
  <footer class="site-footer">
    <div><div class="brand"><span class="brand-dot"></span><div><div class="brand-name">VORLAND COMPOSITES INC</div><div class="brand-sub">Wyoming · North America Distributor</div></div></div><p class="foot-note">Exclusive North America sales partner for BLORAN Composites.</p></div>
    <div><h4 class="foot-head">Explore</h4><div class="foot-links"><a>Product Catalog</a><a>Industries</a><a>About</a><a>Contact</a></div></div>
    <div class="foot-office"><h4 class="foot-head">Head Office</h4><p>Redmesa City, USA</p><p class="mail">sales@vorlandcomposites.com</p><p class="tel">+1 (555) 014-0188</p><small>© 2025 VORLAND COMPOSITES INC. All rights reserved.</small></div>
  </footer>
</section>

<!-- Industries -->
<section class="page page--industries">
  <header class="site-header">
    <div class="brand"><span class="brand-dot"></span><div><div class="brand-name">VORLAND COMPOSITES INC</div><div class="brand-sub">Wyoming · North America Distributor</div></div></div>
    <nav class="nav"><a>Home</a><a>Products</a><a class="is-active">Industries</a><a>About</a><a>Contact</a><a class="quote">Request a Quote</a></nav>
  </header>
  <div class="wrap">
    <h1 class="page-title">Industries</h1>
    <p class="page-sub">From prototyping to certified production, we align materials and processes to your industry standards.</p>
    <table class="ind-table">
      <thead><tr><th style="width:105px">Industry</th><th style="width:275px">Typical Applications</th><th>Recommended Fibers</th></tr></thead>
      <tbody>
        <tr><td>Aerospace</td><td>Primary/secondary structures, interiors, thermal protection</td><td>Carbon, S-Glass, Quartz, High Silica</td></tr>
        <tr><td>Automotive</td><td>Body panels, crash structures, interiors, tooling</td><td>Carbon, Aramid, E-/S-Glass, Basalt</td></tr>
        <tr><td>Construction</td><td>FRP plates, wraps, rebar, façade, fire barriers</td><td>Glass, Basalt, High Silica</td></tr>
        <tr><td>Electrical</td><td>Insulation, laminates, wave-transparent structures</td><td>Quartz, High Silica, Glass</td></tr>
        <tr><td>Machinery &amp; Energy</td><td>Lightweight arms, guards, tanks, wind blades</td><td>Carbon, Glass, Basalt, Alumina</td></tr>
      </tbody>
    </table>
    <div class="band" style="margin-top:14px"><p>Need a materials shortlist mapped to ASTM/FAA/UL targets?</p><span class="btn">Request a Consultation</span></div>
  </div>
  <footer class="site-footer">
    <div><div class="brand"><span class="brand-dot"></span><div><div class="brand-name">VORLAND COMPOSITES INC</div><div class="brand-sub">Wyoming · North America Distributor</div></div></div><p class="foot-note">Exclusive North America sales partner for BLORAN Composites.</p></div>
    <div><h4 class="foot-head">Explore</h4><div class="foot-links"><a>Product Catalog</a><a>Industries</a><a>About</a><a>Contact</a></div></div>
    <div class="foot-office"><h4 class="foot-head">Head Office</h4><p>Redmesa City, USA</p><p class="mail">sales@vorlandcomposites.com</p><p class="tel">+1 (555) 014-0188</p><small>© 2025 VORLAND COMPOSITES INC. All rights reserved.</small></div>
  </footer>
</section>

<!-- Contact -->
<section class="page page--contact">
  <header class="site-header">
    <div class="brand"><span class="brand-dot"></span><div><div class="brand-name">VORLAND COMPOSITES INC</div><div class="brand-sub">Wyoming · North America Distributor</div></div></div>
    <nav class="nav"><a>Home</a><a>Products</a><a>Industries</a><a>About</a><a class="is-active">Contact</a><a class="quote">Request a Quote</a></nav>
  </header>
  <div class="wrap">
    <h1 class="page-title">Contact &amp; RFQ</h1>
    <p class="page-sub">Tell us about your application and volumes. We'll align material, weave, and process to your target properties and budget.</p>
    <form class="rfq">
      <div class="field"><label>Full Name</label><div class="input">First Last</div></div>
      <div class="field"><label>Company</label><div class="input">Company Inc.</div></div>
      <div class="field"><label>Email</label><div class="input">you@example.com</div></div>
      <div class="field"><label>Phone</label><div class="input">+1 555 555 0100</div></div>
      <div class="field"><label>Application / Industry</label><div class="input" style="color:var(--text)">Aerospace<span>⌄</span></div></div>
      <div class="field"><label>Target Material</label><div class="input" style="color:var(--text)">Carbon Fiber<span>⌄</span></div></div>
      <div class="field field--wide"><label>Notes</label><div class="input textarea">We need 200 gsm twill carbon for body panels…</div></div>
      <div class="field"><span class="btn submit">Submit RFQ</span></div>
    </form>
  </div>
  <footer class="site-footer">
    <div><div class="brand"><span class="brand-dot"></span><div><div class="brand-name">VORLAND COMPOSITES INC</div><div class="brand-sub">Wyoming · North America Distributor</div></div></div><p class="foot-note">Exclusive North America sales partner for BLORAN Composites.</p></div>
    <div><h4 class="foot-head">Explore</h4><div class="foot-links"><a>Product Catalog</a><a>Industries</a><a>About</a><a>Contact</a></div></div>
    <div class="foot-office"><h4 class="foot-head">Head Office</h4><p>Redmesa City, USA</p><p class="mail">sales@vorlandcomposites.com</p><p class="tel">+1 (555) 014-0188</p><small>© 2025 VORLAND COMPOSITES INC. All rights reserved.</small></div>
  </footer>
</section>

</body>
</html>
```